Trade Show Design

Two, doublesided backdrops/one doublesided banner/one countertop. I have 3 sample pictures of the 3 items that we are purchasing and all the dimensions are listed on the file names.
website: www.brickwisestudio.net
We are a training center that teaches homeowner's how to do their own home renovations through in-person classes with hands-on training.
We are looking to update our tradeshow displays utilizing stock photos as our photos do not have high enough resolution. I have attached lots of example pictures to select from but some of my favourites that I want to use are over 10 MB so they won't upload. Will have to figure out a different way to upload. Our tagline is tackle any project like a pro. We also use words such as "learn to reno" or "practical, hands-on training". We want to use our current branding (pictures of our minivan are uploaded as well) and our color palette document and really show people what we are all about - classes that people can attend so they can learn to reno their home.
Updates

For the 2 backdrops, we would like them to either be stand-alone or together incase we go to a trade show and only have room for 1 of them. They are to be different designs, front and back but a continuous flow if we are to use them together. Again, I have to figure out how to upload additional pictures as some of the ones I want to use are larger. Thanks!

Same with the Banner that is also double-sided - this is to be a different design for the back and front. We want minimal wording on everything but we really want to showcase what we do so that people can figure it out quickly when they walk by our booth....we offer in-person class with hands-on training. Learn to do by doing. Like on our vehicle that I sent example pictures of, we can put a list of a few topics so that people can understand:
Renovation Topics:
Bathroom
Drywall
Flooring
Tiling
Basement
Framing
Plumbing
Baseboards
Feature Walls

Here is the link to the Vornel Box to additional photos.

https://files.vornelbox.net/shared/7QK4r_mz2-TX8LwBnPe5YuJsdA0fGhRkZ?view=open

Thanks,
Marla

```html
<!DOCTYPE html>
<html lang="en">
<head>
<meta charset="utf-8">
<title>Brickwise Studio – Trade Show Backdrop &amp; Banner</title>
<link rel="stylesheet" href="https://fonts.googleapis.com/css2?family=Anton&family=Poppins:wght@300;600;700&display=swap">
<style>
  :root{
    --page:#d9e1e8;
    --teal:#155e6b;
    --teal-soft:#2a7480;
    --sand:#e7e7b6;
    --olive:#c8c88e;
    --sky:#aac8e8;
    --amber:#d4952c;
    --white:#ffffff;
  }
  *{box-sizing:border-box;margin:0;padding:0}
  html,body{width:942px;height:1200px;overflow:hidden}
  body{background:var(--page);font-family:"Poppins",sans-serif;position:relative}

  /* ---------- main backdrop ---------- */
  .backdrop{
    position:absolute;left:74px;top:77px;width:793px;height:620px;
    display:grid;grid-template-columns:284px 255px 254px;grid-template-rows:216px 218px 186px;
    box-shadow:0 14px 28px rgba(40,60,80,.22);
  }
  .hero-panel{
    grid-row:1/4;grid-column:1;position:relative;
    background:linear-gradient(160deg,#d3d39c 0%,var(--olive) 55%,#b9b880 100%);
  }
  .photo{display:block;width:100%;height:100%}
  .photo.warm{background:linear-gradient(150deg,#eae4de,#c98f85 55%,#b8a89a)}
  .photo.cool{background:linear-gradient(150deg,#c8c0b3,#6b5a55 50%,#b1615a)}
  .photo.floor{background:linear-gradient(160deg,#e8e8e8,#3c4a66 50%,#d9d6d2)}

  .topic{
    display:flex;flex-direction:column;align-items:center;justify-content:center;
    text-align:center;font-weight:700;text-transform:uppercase;line-height:1.42;
    font-size:15px;color:var(--teal);
  }
  .topic svg{margin-bottom:14px}
  .topic.sand{background:var(--sand)}
  .topic.teal{background:var(--teal);color:var(--white)}
  .topic.sky{background:var(--sky)}
  .topic.amber{background:var(--amber);color:var(--white)}

  .brand{position:absolute;left:76px;top:118px;width:160px}
  .brand-name{display:flex;align-items:center;gap:7px;font-weight:700;font-size:15px;color:var(--teal);line-height:1}
  .brand-mark{width:14px;height:14px;background:var(--amber)}
  .brand-tagline{margin-top:5px;font-weight:300;font-size:9.5px;color:var(--teal)}

  .headline{position:absolute;left:28px;top:230px;width:240px;font-family:"Anton",sans-serif;line-height:1;text-align:center}
  .headline .line-1{display:block;font-size:54px;color:var(--teal)}
  .headline .line-2{
    display:block;margin:2px 0 0 2px;width:226px;padding:4px 0 8px;font-size:50px;color:var(--white);
    background:var(--amber);border-radius:6px;transform:rotate(-2deg);
  }
  .headline .line-3{display:block;margin-top:2px;font-size:54px;color:var(--teal)}
  .underline{position:absolute;left:60px;top:424px}

  .url-pill{
    position:absolute;left:55px;top:533px;display:flex;align-items:center;
    height:30px;width:174px;background:var(--teal);border-radius:15px;
    color:var(--white);font-size:10.5px;
  }
  .url-pill .dot{width:32px;height:32px;border-radius:50%;background:var(--amber);display:flex;align-items:center;justify-content:center;margin:0 12px 0 -2px}

  /* ---------- banner ---------- */
  .banner{
    position:absolute;left:256px;top:752px;width:430px;height:356px;
    display:grid;grid-template-columns:repeat(12,1fr);grid-template-rows:124px 124px 108px;
    box-shadow:0 14px 28px rgba(40,60,80,.22);
  }
  .banner .topic{font-size:8.5px;line-height:1.45}
  .banner .topic svg{margin-bottom:7px}
  .b-photo-1{grid-column:1/4;background:linear-gradient(160deg,#eee,#a28a70 60%,#d9c7b0)}
  .b-logo{grid-column:4/7;background:var(--sand);display:flex;align-items:center;justify-content:center;flex-direction:column}
  .b-logo .brand-name{font-size:10px;gap:5px}
  .b-logo .brand-mark{width:9px;height:9px}
  .b-logo .brand-tagline{font-size:6.5px;margin-top:3px}
  .b-photo-2{grid-column:7/10;background:linear-gradient(160deg,#555,#a07a62 55%,#3f5c7a)}
  .b-drywall{grid-column:10/13}
  .b-tiling{grid-column:1/4}
  .b-title{
    grid-column:4/10;background:var(--teal-soft);display:flex;flex-direction:column;align-items:center;justify-content:center;
    font-family:"Anton",sans-serif;color:var(--white);font-size:38px;line-height:1.05;text-align:center;font-weight:400;
  }
  .b-flooring{grid-column:10/13}
  .b-photo-3{grid-column:1/5;background:linear-gradient(160deg,#f2f2f2,#b9a0b8 50%,#2c3f5a)}
  .b-url{grid-column:5/9;background:var(--sky);display:flex;align-items:center;justify-content:center}
  .b-url .url-pill{position:static;width:100px;height:18px;font-size:6.5px;border-radius:9px}
  .b-url .url-pill .dot{width:19px;height:19px;margin:0 6px 0 -2px}
  .b-photo-4{grid-column:9/13;background:linear-gradient(160deg,#8a7566,#3a4d63 55%,#d5c4b0)}
</style>
</head>
<body>

<section class="backdrop" aria-label="Trade show backdrop">
  <div class="hero-panel" role="img" aria-label="Toned photo of a woman in safety glasses sanding wood">
    <div class="brand">
      <div class="brand-name"><span class="brand-mark"></span>Brickwise Studio</div>
      <div class="brand-tagline">Build it right, room by room.</div>
    </div>
    <h1 class="headline">
      <span class="line-1">Practical,</span>
      <span class="line-2">Hands-on</span>
      <span class="line-3">Training.</span>
    </h1>
    <svg class="underline" width="140" height="8" viewBox="0 0 140 8"><path d="M2 6 C40 2 90 3 138 4" stroke="#d4952c" stroke-width="1.6" fill="none"/></svg>
    <div class="url-pill">
      <span class="dot"><svg width="10" height="12" viewBox="0 0 10 12"><path d="M1 1 L1 10 L3.5 7.8 L5.5 11.5 L7 10.8 L5 7.2 L8.5 7 Z" fill="#fff"/></svg></span>
      brickwisestudio.net
    </div>
  </div>

  <div class="photo warm" role="img" aria-label="Photo of a couple installing a ceiling light fixture"></div>

  <div class="topic sand">
    <svg width="52" height="52" viewBox="0 0 52 52" fill="#155e6b"><rect x="6" y="26" width="40" height="20" rx="2"/><rect x="14" y="6" width="5" height="20"/><rect x="10" y="4" width="13" height="7" rx="2"/><rect x="27" y="10" width="6" height="16"/><path d="M36 8 a6 6 0 1 1 8 4 L42 26 h-5 z"/><rect x="10" y="34" width="32" height="4" fill="#e7e7b6"/></svg>
    Flooring<br>Baseboards<br>Basement
  </div>

  <div class="topic teal">
    <svg width="52" height="44" viewBox="0 0 52 44" fill="#fff"><rect x="2" y="2" width="32" height="14" rx="4"/><rect x="34" y="6" width="8" height="6"/><rect x="42" y="8" width="9" height="2"/><rect x="10" y="16" width="12" height="16"/><rect x="6" y="32" width="20" height="10" rx="2"/></svg>
    Drywall<br>Feature Walls<br>Framing
  </div>

  <div class="photo cool" role="img" aria-label="Photo of two friends sitting on the floor working with a toolbox"></div>

  <div class="photo floor" role="img" aria-label="Photo of a couple laying laminate floor planks"></div>

  <div class="topic sky">
    <svg width="48" height="48" viewBox="0 0 48 48" fill="none" stroke="#155e6b" stroke-width="3"><path d="M8 46 V14 a10 10 0 0 1 18 -6"/><path d="M18 16 a12 12 0 0 1 20 0 z" fill="#155e6b"/><g stroke-width="2" stroke-dasharray="3 3"><path d="M22 22 L18 36"/><path d="M28 22 L27 38"/><path d="M33 21 L37 36"/><path d="M37 19 L45 30"/></g></svg>
    Tiling<br>Bathroom<br>Plumbing
  </div>
</section>

<section class="banner" aria-label="Trade show banner">
  <div class="b-photo-1" role="img" aria-label="Photo of a couple with tool belts and a drill"></div>
  <div class="b-logo">
    <div class="brand-name"><span class="brand-mark"></span>Brickwise Studio</div>
    <div class="brand-tagline">Build it right, room by room.</div>
  </div>
  <div class="b-photo-2" role="img" aria-label="Photo of a smiling woman using a hammer"></div>
  <div class="topic amber b-drywall">
    <svg width="28" height="24" viewBox="0 0 52 44" fill="#fff"><rect x="2" y="2" width="32" height="14" rx="4"/><rect x="34" y="6" width="8" height="6"/><rect x="42" y="8" width="9" height="2"/><rect x="10" y="16" width="12" height="16"/><rect x="6" y="32" width="20" height="10" rx="2"/></svg>
    Drywall<br>Feature Walls<br>Framing
  </div>

  <div class="topic sand b-tiling">
    <svg width="26" height="26" viewBox="0 0 48 48" fill="none" stroke="#155e6b" stroke-width="3"><path d="M8 46 V14 a10 10 0 0 1 18 -6"/><path d="M18 16 a12 12 0 0 1 20 0 z" fill="#155e6b"/><g stroke-width="2" stroke-dasharray="3 3"><path d="M22 22 L18 36"/><path d="M28 22 L27 38"/><path d="M33 21 L37 36"/><path d="M37 19 L45 30"/></g></svg>
    Tiling<br>Bathroom<br>Plumbing
  </div>
  <h2 class="b-title">Learn<br>To Reno
    <svg width="74" height="8" viewBox="0 0 74 8"><path d="M2 6 C25 2 50 2 72 4" stroke="#d4952c" stroke-width="1.4" fill="none"/></svg>
  </h2>
  <div class="topic sky b-flooring">
    <svg width="28" height="28" viewBox="0 0 52 52" fill="#155e6b"><rect x="6" y="26" width="40" height="20" rx="2"/><rect x="14" y="6" width="5" height="20"/><rect x="10" y="4" width="13" height="7" rx="2"/><rect x="27" y="10" width="6" height="16"/><path d="M36 8 a6 6 0 1 1 8 4 L42 26 h-5 z"/><rect x="10" y="34" width="32" height="4" fill="#aac8e8"/></svg>
    Flooring<br>Baseboards<br>Basement
  </div>

  <div class="b-photo-3" role="img" aria-label="Photo of two people holding renovation tools"></div>
  <div class="b-url">
    <div class="url-pill">
      <span class="dot"><svg width="6" height="8" viewBox="0 0 10 12"><path d="M1 1 L1 10 L3.5 7.8 L5.5 11.5 L7 10.8 L5 7.2 L8.5 7 Z" fill="#fff"/></svg></span>
      brickwisestudio.net
    </div>
  </div>
  <div class="b-photo-4" role="img" aria-label="Photo of a woman in safety glasses drilling wood"></div>
</section>

</body>
</html>
```